IV Nutritional Clinic Web Design

We are working with Velqo. They are an IV Nutritional Clinic and in need of a new website design.
Some sites to use for inspiration:
https://brightpathcareco.com
https://www.ourzavrowellness.com
https://www.dewspringlounge.com
https://qvitalsurge.com
https://www.lumo-vital.com/pages/iv-therapy-west-hollywood
https://www.tqoncologyhub.com/cancer-care/iv-drips/
https://dripwellary.com
https://corvinahealthhub.com
Thank you for taking the time to consider designing a website for us. We are web developers based in Stockton, CA, USA. Most of our projects go through the same process. Understanding this process may help you win a project with us. We custom-code all of our websites in-house. We don’t have any requirements as to what tools you use for your design, but we prefer Figma files. For any design that we label as four-stars, we send it to the client for review. The client picks the final design they want us to use. Once we complete this process, we will continue to show additional clients all the four-star sites and purchase them later. Your designs will have multiple chances to sell. For better chances of success, we ask that you follow these guidelines.
IMAGES:
If you use any images or icons in the design, we ask that you have a link to the asset so we can purchase the image/icon. Most of the designs we submit do not have the customer’s images on them unless they have some great images. Be creative; show us the feeling you are trying to portray with your image choices. Use any royalty-free site you choose. We subscribe to Pixvane and mainly use their images, but we can purchase images outside of Pixvane.
PLEASE NOTE: we will not submit designs to clients with watermarks on the images.
FONTS:
We ask that you identify the fonts used in the design. This can be done in a message if you want. We typically use Google Fonts and Pixvane Fonts.
CONTENT:
We're always open to different content and ideas. We often submit designs with stock images so the client can see our vision. We typically take pictures after the website launch to use their images with our vision. Lorem Ipsum is fine for paragraphs, but we ask that you write the headers in correct English. We want to be able to show the vision and identify the sections of the website.
INSPIRATION:
We typically add a couple of links in the brief of websites we like to help you get started in your design.
REVISIONS:
We do not often ask for revisions of the designs unless we see something in the design that may not appeal to the client. If there are slight changes that we want to make, we do that in the development process.
FEEDBACK:
We rarely give feedback on designs during the design process. We are working on many website projects and do not have the time to provide feedback. We usually respond if your request is well thought out and asks specific questions, but a note asking “feedback, please” usually goes unanswered.

```html
<!DOCTYPE html>
<html lang="en">
<head>
<meta charset="utf-8">
<title>Velqo Hydration – IV Wellness Clinic</title>
<link href="https://fonts.googleapis.com/css2?family=Poppins:wght@400;500;600;700&display=swap" rel="stylesheet">
<style>
:root{
  --navy:#1d2a8c;
  --navy-deep:#1b2480;
  --green:#78a53a;
  --green-deep:#5a8a2b;
  --green-dark:#4e7d25;
  --ink:#3a3a3a;
  --muted:#555;
  --white:#fff;
  --line:#d9d9d9;
}
*{box-sizing:border-box;margin:0;padding:0}
html,body{width:1200px;height:3394px;overflow:hidden}
body{font-family:'Poppins',sans-serif;color:var(--ink);background:var(--white);position:relative}
.abs{position:absolute}
a{color:inherit;text-decoration:none}

.top-strip{top:0;left:0;width:1200px;height:16px;background:var(--green)}
.site-header{top:16px;left:0;width:1200px;height:96px;background:var(--white)}
.brand{left:111px;top:30px;font-weight:700;font-size:44px;color:var(--navy);letter-spacing:2px;line-height:1}
.main-nav{left:327px;top:38px;display:flex;gap:39px;font-size:14px;color:#444}
.main-nav .active{color:var(--navy);font-weight:600;border-bottom:2px solid var(--navy);padding-bottom:8px}
.btn-outline{border:1.5px solid var(--navy);color:var(--navy);border-radius:8px;font-size:14px;font-weight:500;display:flex;align-items:center;justify-content:center}
.btn-green{background:var(--green);color:var(--white);border-radius:8px;font-size:14px;font-weight:500;display:flex;align-items:center;justify-content:center}

.hero{top:112px;left:0;width:1200px;height:454px;background:linear-gradient(90deg,#3f55a8 0%,#6778b8 40%,#c9ccd8 70%,#e6e2dc 100%)}
.hero h1{position:absolute;left:111px;top:98px;font-size:44px;line-height:58px;font-weight:600;color:var(--white);width:620px}
.hero p{position:absolute;left:111px;top:238px;font-size:17px;line-height:27px;color:var(--white);width:520px}

.eyebrow{font-size:18px;font-weight:500;color:var(--navy);letter-spacing:.3px}
.eyebrow.light{color:var(--white)}
.title-green{font-size:37px;line-height:45px;font-weight:600;color:var(--green)}

.service-card .photo{width:203px;height:170px}
.service-card h3{font-size:16px;font-weight:500;color:var(--green);margin-top:24px;letter-spacing:.2px}
.service-card p{font-size:14px;line-height:23px;color:var(--muted);margin-top:14px}
.read-more{display:inline-block;margin-top:12px;font-size:12px;font-weight:500;color:var(--navy);border-bottom:1px solid var(--navy)}

.about-band{top:1064px;left:0;width:1200px;height:1083px;background:linear-gradient(135deg,var(--green-deep),#65952f 50%,var(--green-dark))}
.dots{left:63px;top:1425px}
.about-text{left:620px;top:1142px;width:470px;color:var(--white)}
.about-text h2{font-size:36px;line-height:45px;font-weight:600;margin-top:16px}
.about-text p{font-size:15px;line-height:23px;margin-top:30px}
.divider{top:1642px;left:111px;width:977px;height:1px;background:rgba(255,255,255,.7)}
.treat-head{top:1726px;left:0;width:1200px;text-align:center;color:var(--white)}
.treat-head h2{font-size:36px;font-weight:600;margin-top:8px}
.treat{top:1857px;width:230px;text-align:center;color:var(--white)}
.treat svg{width:106px;height:106px}
.treat h3{font-size:16px;font-weight:500;margin-top:34px}
.treat p{font-size:14px;line-height:20px;margin-top:10px}

.blog-head{top:2228px;left:0;width:1200px;text-align:center}
.blog-card{top:2345px;width:301px;height:327px;border:1px solid #bbb;border-radius:6px;overflow:hidden;background:var(--white)}
.blog-card .photo{height:203px}
.blog-card h3{font-size:19px;font-weight:400;line-height:29px;color:#222;padding:14px 14px 0}
.blog-card .meta{position:absolute;left:14px;bottom:14px;font-size:12px;color:#444;display:flex;align-items:center;gap:6px}
.blog-card .go{position:absolute;right:0;bottom:0;width:44px;height:36px;background:var(--green);display:flex;align-items:center;justify-content:center}

.map{top:2760px;left:0;width:1200px;height:307px;background:linear-gradient(180deg,#eef0f2,#e7eaee)}

.site-footer{top:3067px;left:0;width:1200px;height:283px;background:var(--navy-deep);color:var(--white)}
.footer-brand{left:111px;top:68px;font-size:58px;font-weight:700;letter-spacing:3px;line-height:1}
.footer-about{left:111px;top:180px;width:270px;font-size:14px;line-height:24px}
.footer-col h4{font-size:18px;font-weight:500;margin-bottom:12px}
.footer-col li{list-style:none;font-size:14px;line-height:27.5px}
.info-row{display:flex;gap:16px;font-size:14px;line-height:21px;margin-bottom:10px}
.info-row svg{flex:none;margin-top:3px}
.bottom-bar{top:3350px;left:0;width:1200px;height:44px;background:var(--green);color:var(--white);font-size:13px;display:flex;align-items:center;justify-content:center}
</style>
</head>
<body>

<div class="abs top-strip"></div>
<header class="abs site-header">
  <div class="abs brand">VELQO</div>
  <nav class="abs main-nav">
    <a class="active">HOME</a><a>ABOUT US</a><a>SERVICES</a><a>LOCATION</a><a>BLOG</a>
  </nav>
  <a class="abs btn-outline" style="left:808px;top:30px;width:134px;height:36px">CONTACT US</a>
  <a class="abs btn-green" style="left:958px;top:30px;width:130px;height:36px;font-size:15px">BOOK NOW</a>
</header>

<section class="abs hero" role="img" aria-label="Woman relaxing during an IV drip with a fruit-filled IV bag in the foreground">
  <h1>Experience the Ultimate in Wellness and Hydration</h1>
  <p>Lorem ipsum dolor sit amet, consectetur adipiscing elit, sed do eiusmod tempor incididunt</p>
  <a class="abs btn-green" style="left:111px;top:304px;width:131px;height:36px;font-size:15px">BOOK NOW</a>
</section>

<section>
  <div class="abs eyebrow" style="left:111px;top:646px">OUR SERVICES</div>
  <h2 class="abs title-green" style="left:111px;top:678px;width:280px">Vitamin Boost Drips</h2>
  <p class="abs" style="left:111px;top:790px;width:290px;font-size:15px;line-height:23px;color:var(--muted)">Lorem ipsum dolor sit amet, consec adipiscing elit, sed do eiusmod tempor incididunt ut labore et dolore magna aliqua. Quis suspendisse ultrices gravida.</p>
  <a class="abs btn-outline" style="left:111px;top:921px;width:170px;height:36px;font-size:15px">SEE ALL SERVICES</a>

  <article class="abs service-card" style="left:432px;top:652px;width:205px">
    <div class="photo" role="img" aria-label="Smiling woman receiving hydration therapy" style="background:linear-gradient(160deg,#ececec,#d9cfc7)"></div>
    <h3>HYDRATION THERAPY</h3>
    <p>Lorem ipsum dolor sit am consec adipiscing elit, sed do eiusmod tempor</p>
    <a class="read-more">READ MORE →</a>
  </article>
  <article class="abs service-card" style="left:659px;top:652px;width:205px">
    <div class="photo" role="img" aria-label="Fruit slices in an IV bag" style="background:linear-gradient(160deg,#8a6b4a,#c7a35d 50%,#7f9a3a)"></div>
    <h3>NUTRIENT INFUSIONS</h3>
    <p>Lorem ipsum dolor sit am consec adipiscing elit, sed do eiusmod tempor</p>
    <a class="read-more">READ MORE →</a>
  </article>
  <article class="abs service-card" style="left:886px;top:652px;width:205px">
    <div class="photo" role="img" aria-label="Gloved clinician preparing an IV line" style="background:linear-gradient(160deg,#cfd6df,#6f86b8 60%,#3f56a8)"></div>
    <h3>ANTI-AGING IV THERAPY</h3>
    <p>Lorem ipsum dolor sit am consec adipiscing elit, sed do eiusmod tempor</p>
    <a class="read-more">READ MORE →</a>
  </article>
</section>

<section class="abs about-band"></section>
<div class="abs" style="left:111px;top:1150px;width:138px;height:125px;background:var(--navy)"></div>
<div class="abs" style="left:429px;top:1403px;width:139px;height:126px;background:var(--navy)"></div>
<div class="abs" role="img" aria-label="Doctor holding an IV bag filled with fruit" style="left:126px;top:1166px;width:425px;height:348px;background:linear-gradient(150deg,#e9edf1,#cbd4dc 60%,#b8c2cc)"></div>
<svg class="abs dots" width="140" height="135" viewBox="0 0 140 135" aria-hidden="true">
  <g fill="#1d2a8c">
    <circle cx="4" cy="4" r="3"/><circle cx="25" cy="4" r="3"/><circle cx="46" cy="4" r="3"/>
    <circle cx="4" cy="25" r="3"/><circle cx="25" cy="25" r="3"/><circle cx="46" cy="25" r="3"/>
    <circle cx="4" cy="46" r="3"/><circle cx="25" cy="46" r="3"/><circle cx="46" cy="46" r="3"/>
    <circle cx="4" cy="67" r="3"/><circle cx="25" cy="67" r="3"/><circle cx="46" cy="67" r="3"/>
    <circle cx="4" cy="88" r="3"/><circle cx="25" cy="88" r="3"/><circle cx="46" cy="88" r="3"/><circle cx="67" cy="88" r="3"/><circle cx="88" cy="88" r="3"/><circle cx="109" cy="88" r="3"/><circle cx="130" cy="88" r="3"/>
    <circle cx="4" cy="109" r="3"/><circle cx="25" cy="109" r="3"/><circle cx="46" cy="109" r="3"/><circle cx="67" cy="109" r="3"/><circle cx="88" cy="109" r="3"/><circle cx="109" cy="109" r="3"/><circle cx="130" cy="109" r="3"/>
  </g>
</svg>
<div class="abs about-text">
  <div class="eyebrow light">ABOUT US</div>
  <h2>Your Trusted Partner for IV Wellness Solutions</h2>
  <p>Sed ut perspiciatis unde omnis iste natus error sit voluptatem accusantium doloremque laudantium, totam rem aperiam, eaque ipsa quae ab illo inventore veritatis et quasi architecto beatae vitae dicta sunt explicabo. Nemo enim ipsam voluptatem quia voluptas sit aspernatur aut odit aut fugit, sed quia consequuntur magni dolores eos qui ratione voluptatem sequi nesciunt neque porro quisquam est,&nbsp; qui dolorem ipsum quia dolor sit amet</p>
</div>
<a class="abs btn-green" style="left:620px;top:1495px;width:144px;height:36px;font-size:15px;background:#86b346">READ MORE</a>

<div class="abs divider"></div>
<div class="abs treat-head">
  <div class="eyebrow light">OUR TREATMENTS</div>
  <h2>IV Therapy for Recovery, Energy, and Vitality</h2>
</div>

<div class="abs treat" style="left:101px">
  <svg viewBox="0 0 106 106" fill="none" stroke="#fff" stroke-width="3" aria-hidden="true">
    <rect x="6" y="6" width="94" height="94" rx="14"/><path d="M26 32a34 22 0 0 1 54 0l-8 12H34z"/><path d="M53 40l6-10"/>
    <path d="M20 62h78v24H38"/><path d="M30 62v8M42 62v6M54 62v8M66 62v6M78 62v8M90 62v6"/>
  </svg>
  <h3>WEIGHT LOSS</h3><p>Lorem ipsum dolor sit am consec adipiscing elit, sed do</p>
</div>
<div class="abs treat" style="left:358px">
  <svg viewBox="0 0 106 106" fill="none" stroke="#fff" stroke-width="3" aria-hidden="true">
    <circle cx="53" cy="53" r="14"/><circle cx="18" cy="16" r="10"/><circle cx="88" cy="16" r="10"/><circle cx="14" cy="88" r="10"/><circle cx="90" cy="84" r="10"/><circle cx="53" cy="92" r="8"/>
    <path d="M25 23l18 19M81 23L63 42M21 81l21-19M83 77L65 61M53 67v17"/>
  </svg>
  <h3>PEPTIDE THERAPY</h3><p>Lorem ipsum dolor sit am consec adipiscing elit, sed do</p>
</div>
<div class="abs treat" style="left:615px">
  <svg viewBox="0 0 106 106" fill="none" stroke="#fff" stroke-width="3" aria-hidden="true">
    <path d="M6 104V4h10v100M16 8h30"/><rect x="30" y="12" width="40" height="50" rx="8"/>
    <path d="M40 24h20M40 32h20M40 40h20M40 48h20"/><path d="M50 62v12a8 8 0 0 1-8 8"/><path d="M50 74c0 12 14 12 14 0V66"/>
    <path d="M64 66c10 0 16 10 16 20v14h12V80"/>
  </svg>
  <h3>IV DRIP INFUSIONS</h3><p>Lorem ipsum dolor sit am consec adipiscing elit, sed do</p>
</div>
<div class="abs treat" style="left:872px">
  <svg viewBox="0 0 106 106" fill="none" stroke="#fff" stroke-width="3" aria-hidden="true">
    <circle cx="42" cy="12" r="8"/><circle cx="28" cy="30" r="6"/>
    <path d="M20 56a14 14 0 0 1 18-20a20 20 0 0 1 36-2a18 18 0 0 1 20 22a16 16 0 0 1-18 26a18 18 0 0 1-30 0a16 16 0 0 1-26-26z"/>
    <text x="48" y="70" fill="#fff" stroke="none" font-family="Poppins,sans-serif" font-size="22">0</text>
    <text x="64" y="80" fill="#fff" stroke="none" font-family="Poppins,sans-serif" font-size="14">3</text>
  </svg>
  <h3>OZONE THERAPY</h3><p>Lorem ipsum dolor sit am consec adipiscing elit, sed do</p>
</div>

<div class="abs blog-head">
  <div class="eyebrow">LATEST BLOG</div>
  <h2 class="title-green" style="margin-top:6px">Boost Your Immunity with IV Infusions</h2>
</div>

<article class="abs blog-card" style="left:111px">
  <div class="photo" role="img" aria-label="Close-up of an IV drip chamber" style="background:linear-gradient(160deg,#2f5a6e,#9ab3c0 50%,#c98a6a)"></div>
  <h3>Lorem ipsum dolor sit amet, consectetur</h3>
  <div class="meta"><svg width="11" height="11" viewBox="0 0 12 12"><circle cx="6" cy="6" r="5" fill="#78a53a"/></svg>3 Comments <span style="margin:0 4px">|</span><svg width="10" height="11" viewBox="0 0 10 11"><circle cx="5" cy="3" r="2.5" fill="#78a53a"/><path d="M0 11a5 5 0 0 1 10 0z" fill="#78a53a"/></svg>Admin</div>
  <div class="go"><svg width="16" height="12" viewBox="0 0 16 12" fill="none" stroke="#fff" stroke-width="2"><path d="M1 6h13M9 1l5 5-5 5"/></svg></div>
</article>
<article class="abs blog-card" style="left:450px">
  <div class="photo" role="img" aria-label="Man resting beside a fruit-filled IV bag" style="background:linear-gradient(160deg,#4a3c34,#8b7b6e 50%,#c7b08a)"></div>
  <h3>Lorem ipsum dolor sit amet, consectetur</h3>
  <div class="meta"><svg width="11" height="11" viewBox="0 0 12 12"><circle cx="6" cy="6" r="5" fill="#78a53a"/></svg>3 Comments <span style="margin:0 4px">|</span><svg width="10" height="11" viewBox="0 0 10 11"><circle cx="5" cy="3" r="2.5" fill="#78a53a"/><path d="M0 11a5 5 0 0 1 10 0z" fill="#78a53a"/></svg>Admin</div>
  <div class="go"><svg width="16" height="12" viewBox="0 0 16 12" fill="none" stroke="#fff" stroke-width="2"><path d="M1 6h13M9 1l5 5-5 5"/></svg></div>
</article>
<article class="abs blog-card" style="left:788px">
  <div class="photo" role="img" aria-label="Row of IV bottles in a clinic" style="background:linear-gradient(160deg,#e4e8ec,#b9c7d0 60%,#9fb6c2)"></div>
  <h3>Lorem ipsum dolor sit amet, consectetur</h3>
  <div class="meta"><svg width="11" height="11" viewBox="0 0 12 12"><circle cx="6" cy="6" r="5" fill="#78a53a"/></svg>3 Comments <span style="margin:0 4px">|</span><svg width="10" height="11" viewBox="0 0 10 11"><circle cx="5" cy="3" r="2.5" fill="#78a53a"/><path d="M0 11a5 5 0 0 1 10 0z" fill="#78a53a"/></svg>Admin</div>
  <div class="go"><svg width="16" height="12" viewBox="0 0 16 12" fill="none" stroke="#fff" stroke-width="2"><path d="M1 6h13M9 1l5 5-5 5"/></svg></div>
</article>

<div class="abs map" role="img" aria-label="Street map showing the clinic location"></div>

<footer class="abs site-footer">
  <div class="abs footer-brand">VELQO</div>
  <p class="abs footer-about">Lorem ipsum dolor sit amet, consectetur adipiscing elit, sed do eiusmod tempor incididunt</p>
  <div class="abs footer-col" style="left:444px;top:61px">
    <h4>QUICK LINKS</h4>
    <ul><li>Home</li><li>About Us</li><li>Services</li><li>Location</li><li>Blog</li></ul>
  </div>
  <div class="abs footer-col" style="left:630px;top:61px">
    <h4>OTHER LINKS</h4>
    <ul><li>FAQs</li><li>Contact Us</li><li>Privacy Policy</li><li>Terms &amp; Conditions</li><li>Sitemaps</li></ul>
  </div>
  <div class="abs footer-col" style="left:850px;top:61px;width:250px">
    <h4>Company Info</h4>
    <div class="info-row" style="margin-top:18px"><svg width="18" height="14" viewBox="0 0 18 14"><path d="M1 2l5-1 6 2 5-1v11l-5 1-6-2-5 1z" fill="#fff"/></svg><span>124, Sed ut perspiciatis unde omnis iste natus</span></div>
    <div class="info-row"><svg width="18" height="16" viewBox="0 0 16 16"><path d="M3 1l3 3-2 2a10 10 0 0 0 6 6l2-2 3 3-2 2C7 15 1 9 1 3z" fill="#fff"/></svg><span>+1 8888- 888-888</span></div>
    <div class="info-row"><svg width="18" height="13" viewBox="0 0 18 13"><rect x="1" y="1" width="16" height="11" rx="1" fill="#fff"/><path d="M1 2l8 6 8-6" stroke="#1b2480" stroke-width="1.5" fill="none"/></svg><span>info@velqo.com</span></div>
  </div>
</footer>
<div class="abs bottom-bar">© 2025 Velqo Hydration. All rights reserved.</div>

</body>
</html>
```